New Payments Start-up requires Logo, Style Guide and Web Site Design

We need a logo, style guide (colour templates etc.) and marketing web-site (HTML/CSS styling) for Fenwu, a new account-to-account payment product for use in the Single European Payment Area (SEPA).

The design is for the product only, not a company brand. We're looking for basic palette and style guidelines also. The web site need only be a basic responsive cross-platform design and layout. We will produce our own content.

We have no requirements for specific colours or logo styles. It is a financial product, however, so should not appear too quirky or untrustworthy.

The product is still in the early phases of development, so we're not able to provide pictures or other content.

As a little more detail on how things work, though, our end customers will arrive at our site through redirection from our merchant partners (a number of whom are large multi-national companies) who have offered our services as an alternative to credit card payments. They will be able to set up a SEPA direct debit mandate online in just a few pages, secure that with a password and use it to pay both immediately and in future with a simple confirmation of the password… a quick, easy checkout.

Because we work with large customer in the payments space, whilst we’d like the brand to be modern and appealing, it has to engender trust and stability. Whilst this product is new and in start-up phase, our company has been in alternative payments for nearly 10 years and have strong products in Europe in the Pre-Paid Zelo/TrevinCard and Voucher space. We'd like to treat this separately, however, which is why we've briefed accordingly.

Reason: Apologies for the extension, but I had a couple of designers contact me to say they had completed work but were unable to submit because time ran out. I'll only extend this once, though, because we need to get cracking on the project. Many thanks Jem

Target Market(s)

European alternative payment customers

Industry/Entity Type

Financial

Logo Text

fenwu

Coding

Coded - Design and coding required

Number of Pages Required

1 page

Font styles to use
Sans Serif

```html
<!DOCTYPE html>
<html lang="en">
<head>
<meta charset="utf-8">
<title>Fenwu — Account-to-Account Payments</title>
<link href="https://fonts.googleapis.com/css2?family=Roboto+Condensed:wght@400;700&family=Roboto:wght@300;400;500&family=Open+Sans:wght@400;600&display=swap" rel="stylesheet">
<style>
:root{
  --blue:#1b7ac7;
  --blue-deep:#1a6aa8;
  --orange:#ec8a1f;
  --ink:#333;
  --muted:#666;
  --soft:#f6f6f6;
  --line:#e2e2e2;
  --navy:#0f2236;
  --red:#d9363e;
  --olive:#6b6b3a;
}
*{box-sizing:border-box;margin:0;padding:0}
html,body{width:679px;height:1200px;overflow:hidden;background:#fff}
body{position:relative;font-family:"Open Sans",Arial,sans-serif;color:var(--ink)}
.abs{position:absolute}
.header{left:0;top:0;width:679px;height:54px;background:#fff;box-shadow:0 1px 3px rgba(0,0,0,.12);z-index:2}
.brand{left:56px;top:11px;display:flex;align-items:center;gap:7px}
.brand-dot{width:30px;height:30px;border-radius:50%;background:var(--blue)}
.brand-name{font-family:"Roboto Condensed",sans-serif;font-weight:700;font-size:22px;color:var(--blue);line-height:1}
.nav{top:24px;font-family:"Roboto",sans-serif;font-size:7.5px;color:#777;letter-spacing:.2px}
.btn-signup{left:526px;top:19px;width:46px;height:17px;background:#4a8fd8;color:#fff;border-radius:2px;font:500 7px "Roboto",sans-serif;display:flex;align-items:center;justify-content:center}
.btn-login{left:578px;top:19px;width:46px;height:17px;border:1px solid var(--red);color:var(--red);border-radius:2px;font:500 7px "Roboto",sans-serif;display:flex;align-items:center;justify-content:center}
.hero{left:0;top:54px;width:679px;height:321px;background:linear-gradient(100deg,#e9e6e1 0%,#d8d3cb 35%,#c9d7e6 55%,#e8e2d8 80%,#d9d2c6 100%)}
.hero-title{left:55px;top:122px;font:700 28px "Roboto Condensed",sans-serif;color:var(--blue);line-height:1}
.hero-sub{left:55px;top:152px;font:700 14px "Roboto Condensed",sans-serif;color:var(--blue)}
.hero-text{left:56px;top:173px;width:220px;font-size:8px;line-height:12px;color:#444}
.hero-arrow{top:211px;width:20px;height:20px;border-radius:50%;background:rgba(80,80,80,.55)}
.welcome{left:0;top:404px;width:679px;text-align:center;font:400 24px "Roboto Condensed",sans-serif;color:var(--ink)}
.welcome span{color:var(--blue)}
.welcome-text{left:94px;top:441px;width:492px;text-align:center;font-size:7px;line-height:13.6px;color:#555}
.btn-primary{left:310px;top:494px;width:70px;height:20px;background:var(--blue);color:#fff;border-radius:2px;font:400 7.5px "Roboto",sans-serif;display:flex;align-items:center;justify-content:center}
.feature{top:547px;width:340px;height:203px;color:#fff;padding:37px 0 0 55px}
.feature-blue{left:0;background:linear-gradient(135deg,#2a6aa0,#1f77b8 60%,#2b6b9b)}
.feature-orange{left:340px;width:339px;background:linear-gradient(135deg,#e98a25,#ef8d1d 60%,#d97d1c);padding-left:34px}
.feature h2{font:400 17.5px "Roboto Condensed",sans-serif;letter-spacing:.2px}
.feature p{margin-top:6px;width:240px;font-size:6.3px;line-height:11.5px}
.feature ul{list-style:none;margin-top:8px}
.feature li{font-size:7.3px;height:17px;display:flex;align-items:center;gap:6px}
.how{left:0;top:750px;width:679px;height:306px;background:var(--soft)}
.how-title{left:0;top:773px;width:679px;text-align:center;font:400 21px "Roboto",sans-serif;color:#444}
.how-rule{left:319px;top:809px;width:42px;height:1px;background:var(--blue)}
.step{top:833px;width:170px;text-align:center}
.step-photo{width:94px;height:94px;border-radius:50%;margin:0 auto;border:3px solid #fff;box-shadow:0 0 0 1px #ddd}
.step h3{margin-top:16px;font:300 11px "Roboto",sans-serif;color:#333}
.step p{margin-top:5px;font-size:6.3px;line-height:11.5px;color:#666;padding:0 12px}
.btn-outline{display:inline-flex;align-items:center;gap:4px;margin-top:8px;height:17px;padding:0 8px;border:1px solid var(--olive);color:#555;font:400 6.5px "Roboto",sans-serif;border-radius:1px}
.subscribe{left:0;top:1056px;width:679px;height:56px;background:var(--blue)}
.subscribe-text{left:143px;top:1072px;color:#fff;font:400 8.8px/13px "Roboto",sans-serif}
.subscribe-form{left:322px;top:1074px;width:282px;height:23px;border-radius:12px;background:#fff;overflow:hidden;display:flex}
.subscribe-form .field{flex:1;font-size:6.5px;color:#777;padding-left:13px;display:flex;align-items:center}
.subscribe-form .go{width:71px;background:var(--navy);color:#fff;font:500 7px "Roboto",sans-serif;display:flex;align-items:center;justify-content:center}
.social{left:290px;top:1132px;display:flex;gap:5px}
.social span{width:16px;height:16px;border-radius:50%;background:#777}
.foot-links{left:0;top:1160px;width:679px;text-align:center;font:400 6.2px "Roboto",sans-serif;color:#333;letter-spacing:.2px}
.copy{left:0;top:1175px;width:679px;text-align:center;font-size:6.5px;color:#555}
</style>
</head>
<body>

<header class="abs header">
  <div class="abs brand"><span class="brand-dot"></span><span class="brand-name">Fenwu</span></div>
  <span class="abs nav" style="left:236px">ABOUT</span>
  <span class="abs nav" style="left:278px">CHECKING</span>
  <span class="abs nav" style="left:333px">SAVINGS</span>
  <span class="abs nav" style="left:382px">LOANS</span>
  <span class="abs nav" style="left:424px">EBANKING</span>
  <span class="abs nav" style="left:478px">CONTACT</span>
  <span class="abs btn-signup">SIGN UP</span>
  <span class="abs btn-login">LOGIN</span>
</header>

<section class="abs hero" role="img" aria-label="Photo of a man in a blue checked shirt working on a laptop with paperwork"></section>
<div class="abs hero-title">FENWU</div>
<div class="abs hero-sub">ACCOUNT-TO-ACCOUNT PAYMENTS</div>
<p class="abs hero-text">Lorem ipsum dolor sit amet, consectetur adipiscing sed do eiusmod tempor incididunt ut labore et</p>
<span class="abs hero-arrow" style="left:13px"><svg width="20" height="20"><path d="M11.5 6 7.5 10l4 4" fill="none" stroke="#fff" stroke-width="1.5"/></svg></span>
<span class="abs hero-arrow" style="left:639px"><svg width="20" height="20"><path d="M8.5 6l4 4-4 4" fill="none" stroke="#fff" stroke-width="1.5"/></svg></span>

<h1 class="abs welcome">Welcome to <span>Fenwu</span></h1>
<p class="abs welcome-text">Nemo enim ipsam voluptatem quia voluptas sit aspernatur aut odit aut fugit, sed quia consequuntur magni dolores eos qui ratione voluptatem sequi nesciunt. Neque porro quisquam est, qui dolorem ipsum quia dolor sit amet, consectetur, adipisci velit, sed quia non numquam eius modi tempora incidunt ut labore et dolore magnam aliquam quaerat voluptatem.</p>
<span class="abs btn-primary">READ MORE</span>

<section class="abs feature feature-blue" role="img" aria-label="Blue-tinted photo of a keyboard and phone showing a completed transaction">
  <h2>MOVE MONEY BETWEEN ACCOUNTS</h2>
  <p>Lorem ipsum dolor sit amet, consectetur adipiscing elit, sed do eiusmod tempor incididunt ut labore et dolore magna aliqua. Ut enim ad minim veniam, quis nostrud exercitation ullamco laboris nisi ut aliquip</p>
  <ul>
    <li><svg width="8" height="8"><path d="M1 4.5l2 2L7 2" fill="none" stroke="#fff" stroke-width="1.6"/></svg>Log in to Clearline Online® banking</li>
    <li><svg width="8" height="8"><path d="M1 4.5l2 2L7 2" fill="none" stroke="#fff" stroke-width="1.6"/></svg>Select the Payments tab</li>
    <li><svg width="8" height="8"><path d="M1 4.5l2 2L7 2" fill="none" stroke="#fff" stroke-width="1.6"/></svg>Select the Acct-to-Acct sub tab</li>
    <li><svg width="8" height="8"><path d="M1 4.5l2 2L7 2" fill="none" stroke="#fff" stroke-width="1.6"/></svg>Follow instructions on the screen</li>
  </ul>
</section>
<section class="abs feature feature-orange" role="img" aria-label="Orange-tinted photo of a person using a smartphone">
  <h2>SEND MONEY TO ANYONE</h2>
  <p>Lorem ipsum dolor sit amet, consectetur adipiscing elit, sed do eiusmod tempor incididunt ut labore et dolore magna aliqua. Ut enim ad minim veniam, quis nostrud exercitation ullamco laboris nisi ut aliquip</p>
  <ul>
    <li><svg width="8" height="8"><path d="M1 4.5l2 2L7 2" fill="none" stroke="#fff" stroke-width="1.6"/></svg>Send money to your child at college</li>
    <li><svg width="8" height="8"><path d="M1 4.5l2 2L7 2" fill="none" stroke="#fff" stroke-width="1.6"/></svg>Send a gift to family and friends</li>
    <li><svg width="8" height="8"><path d="M1 4.5l2 2L7 2" fill="none" stroke="#fff" stroke-width="1.6"/></svg>Reimburse friends after a fun night out</li>
    <li><svg width="8" height="8"><path d="M1 4.5l2 2L7 2" fill="none" stroke="#fff" stroke-width="1.6"/></svg>Pay rent to your landlord or roommates</li>
  </ul>
</section>

<section class="abs how"></section>
<h2 class="abs how-title">How It Works</h2>
<span class="abs how-rule"></span>

<article class="abs step" style="left:64px">
  <div class="step-photo" role="img" aria-label="Photo of hands holding a phone in front of a laptop" style="background:linear-gradient(135deg,#c9ccd2,#e9e9ec)"></div>
  <h3>Confirmation of the password</h3>
  <p>Lorem ipsum dolor sit amet, consectetur adipiscing elit, sed do eiusmod tempor incididunt ut labore et dolore magna aliqua.</p>
  <span class="btn-outline">READ MORE <svg width="7" height="5"><path d="M0 2.5h5M3.5 .5l2 2-2 2" fill="none" stroke="#333" stroke-width="1"/></svg></span>
</article>
<article class="abs step" style="left:257px">
  <div class="step-photo" role="img" aria-label="Photo of a hand holding a red payment card over a laptop keyboard" style="background:linear-gradient(135deg,#d9c3b0,#e6e2de 60%,#c9cdd4)"></div>
  <h3>A Quick payment</h3>
  <p>Lorem ipsum dolor sit amet, consectetur adipiscing elit, sed do eiusmod tempor incididunt ut labore et dolore magna aliqua.</p>
  <span class="btn-outline">READ MORE <svg width="7" height="5"><path d="M0 2.5h5M3.5 .5l2 2-2 2" fill="none" stroke="#333" stroke-width="1"/></svg></span>
</article>
<article class="abs step" style="left:441px">
  <div class="step-photo" role="img" aria-label="Photo of a laptop screen showing a login page" style="background:linear-gradient(135deg,#9fb4c8,#dfe6ee 55%,#3a3f47)"></div>
  <h3>Easy Checkout</h3>
  <p>Lorem ipsum dolor sit amet, consectetur adipiscing elit, sed do eiusmod tempor incididunt ut labore et dolore magna aliqua.</p>
  <span class="btn-outline">READ MORE <svg width="7" height="5"><path d="M0 2.5h5M3.5 .5l2 2-2 2" fill="none" stroke="#333" stroke-width="1"/></svg></span>
</article>

<section class="abs subscribe"></section>
<svg class="abs" style="left:44px;top:1060px" width="52" height="50"><g fill="none" stroke="rgba(255,255,255,.15)" stroke-width="2"><rect x="6" y="12" width="40" height="28" rx="3" transform="rotate(-20 26 26)"/><path d="M10 14l16 14 18-18" transform="rotate(-20 26 26)"/></g></svg>
<svg class="abs" style="left:112px;top:1073px" width="22" height="22"><path d="M1 10 21 1 15 21 10 13zM10 13 21 1" fill="none" stroke="#fff" stroke-width="1.5" stroke-linejoin="round"/></svg>
<p class="abs subscribe-text">SUBSCRIBE TO RECEIVE UPDATES AND<br>EXCLUSIVE OFFERS.</p>
<div class="abs subscribe-form"><span class="field">Enter your E - mail</span><span class="go">SUBSCRIBE</span></div>

<div class="abs social" aria-label="Social links"><span></span><span></span><span></span><span></span><span></span></div>
<nav class="abs foot-links">HOME &nbsp;/&nbsp; EBANKING &nbsp;/&nbsp; LOANS &nbsp;/&nbsp; SAVINGS &nbsp;/&nbsp; CHECKING &nbsp;/&nbsp; COMMUNITY &nbsp;/&nbsp; CONTACT US</nav>
<p class="abs copy">2016 © Copyrights Fenwu.All Rights Reserved</p>

</body>
</html>
```